Allied Health team of Physiotherapists & Occupational Therapists seek a business card design

We have our new logo, we now need our new business cards and stationary. Tidewell: Oedema & Family Clinic is seeking a generic card design to represent our whole team and individual cards for each therapist that incorporates our new logo to communicate our holistic approach that is calming, nuturing, supportive and welcoming.
Our Physiotherapists and Occupational Therapists assess, treat and provide education for people who are at risk of or who have lymphoedema. This is often as a result of treatment for cancer. We provide pre-operative and post-operative management and cancer rehabilitation in our Pilates studio. Our team also consists of Physiotherapists who have a strong interest in pelvic floor and continence management for both men and women.

Target Market(s)

Mainly women health conscious

Industry/Entity Type

Allied Health: Physiotherapy / Occupational Therapy

Contact Information for Business Card

Address: 14 Gallivant Ave Larkmoor 3207 Phone: 84316570 fax: 8431 6578 Email: info@tidewellcareservices.com.au Website: tidewellcareservices.com.au Facebook address: facebook.com/TidewellOedemaAndFamilyCareClinic. Room to write appointments. Individual cards need to have name, office email and individual email and professional details

Requirements
Must have
• Logo as per uploaded documents

```html
<!DOCTYPE html>
<html lang="en">
<head>
<meta charset="utf-8">
<title>Tidewell business cards</title>
<link rel="stylesheet" href="https://fonts.googleapis.com/css2?family=Marcellus&family=Roboto:ital,wght@0,400;1,400&display=swap">
<style>
  :root {
    --backdrop: #262626;
    --card-top: #efefef;
    --card-bottom: #e2e2e2;
    --accent: #e0895a;
    --ink: #333333;
    --ring: #d9d9d9;
  }
  html, body {
    margin: 0;
    width: 1200px;
    height: 1138px;
    overflow: hidden;
    background: var(--backdrop);
  }
  .canvas { position: relative; width: 1200px; height: 1138px; }
  .card {
    position: absolute;
    border-radius: 14px;
    background: linear-gradient(180deg, var(--card-top), var(--card-bottom));
  }
  .card--front { left: 93px; top: 246px; width: 376px; height: 624px; }
  .card--back  { left: 494px; top: 385px; width: 619px; height: 374px; }

  .brand {
    position: absolute;
    display: flex;
    flex-direction: column;
    align-items: center;
    justify-content: center;
    text-align: center;
    font-family: "Marcellus", serif;
    color: var(--accent);
    border: 2px solid var(--ring);
    border-radius: 50%;
    box-sizing: border-box;
  }
  .card--front .brand { left: 62px; top: 189px; width: 250px; height: 250px; }
  .card--back .brand  { left: 60px; top: 87px; width: 192px; height: 192px; }
  .brand__name { font-size: 46px; line-height: 1; }
  .brand__sub  { font-size: 15px; line-height: 1.3; margin-top: 8px; }
  .card--back .brand__name { font-size: 36px; }
  .card--back .brand__sub  { font-size: 12px; }

  .details {
    position: absolute;
    left: 296px;
    top: 78px;
    font-family: "Roboto", sans-serif;
    color: var(--ink);
  }
  .details__name {
    font-family: "Marcellus", serif;
    color: var(--accent);
    font-size: 23px;
    margin: 0 0 6px;
    font-weight: 400;
  }
  .details__role { font-style: italic; font-size: 14px; margin: 0; line-height: 19px; }
  .details__focus { font-size: 14px; margin: 0; line-height: 19px; }
  .contacts { list-style: none; padding: 0; margin: 38px 0 0; font-size: 15.5px; }
  .contacts li { display: flex; align-items: center; height: 23.5px; }
  .contacts svg { width: 13px; height: 13px; margin: 0 14px 0 2px; fill: var(--accent); flex: none; }
  .contacts .gap { margin-left: 18px; }
</style>
</head>
<body>
<main class="canvas">
  <section class="card card--front">
    <div class="brand">
      <span class="brand__name">Tidewell</span>
      <span class="brand__sub">Oedema &amp; Family Clinic</span>
    </div>
  </section>

  <section class="card card--back">
    <div class="brand">
      <span class="brand__name">Tidewell</span>
      <span class="brand__sub">Oedema &amp; Family Clinic</span>
    </div>
    <div class="details">
      <h1 class="details__name">Maren Holt</h1>
      <p class="details__role">Physiotherapist</p>
      <p class="details__focus">Lymphoedema &amp; Oncology Rehabilitation</p>
      <p class="details__focus">Continence &amp; Pelvic Floor</p>
      <ul class="contacts">
        <li>
          <svg viewBox="0 0 16 16" aria-hidden="true"><path d="M2 6c0-2 2-3 6-3s6 1 6 3v1h-3V5.5H5V7H2zM4 8h8l1 6H3z"/></svg>
          8431 6570
          <svg class="gap" viewBox="0 0 16 16" aria-hidden="true"><path d="M2 6c0-2 2-3 6-3s6 1 6 3v1h-3V5.5H5V7H2zM4 8h8l1 6H3z"/></svg>
          8431 6578
        </li>
        <li>
          <svg viewBox="0 0 16 16" aria-hidden="true"><path d="M1 3h14v10H1zM2.5 4.5 8 9l5.5-4.5v1L8 10 2.5 5.5z" fill-rule="evenodd"/></svg>
          info@tidewellcareservices.com.au
        </li>
        <li>
          <svg viewBox="0 0 16 16" aria-hidden="true"><path d="M8 1a7 7 0 1 0 0 14A7 7 0 0 0 8 1zm0 1.5c1 1.2 1.6 3 1.7 4.7H6.3C6.4 5.5 7 3.7 8 2.5zM2.6 7.2a5.5 5.5 0 0 1 2.6-4c-.6 1.2-1 2.6-1 4zm0 1.6h1.6c.1 1.4.4 2.8 1 4a5.5 5.5 0 0 1-2.6-4zM8 13.5c-1-1.2-1.6-3-1.7-4.7h3.4c-.1 1.7-.7 3.5-1.7 4.7zm2.8-.3c.6-1.2.9-2.6 1-4h1.6a5.5 5.5 0 0 1-2.6 4zm1-6c0-1.4-.4-2.8-1-4a5.5 5.5 0 0 1 2.6 4z"/></svg>
          www.tidewellcareservices.com.au
        </li>
        <li>
          <svg viewBox="0 0 16 16" aria-hidden="true"><path d="M8 1a5 5 0 0 0-5 5c0 4 5 9 5 9s5-5 5-9a5 5 0 0 0-5-5zm0 7a2 2 0 1 1 0-4 2 2 0 0 1 0 4z"/></svg>
          14 Gallivant Ave, Larkmoor 3207
        </li>
      </ul>
    </div>
  </section>
</main>
</body>
</html>
```